Ridgeline Haul Carriers - Website

A clean, not cluttered informative website for our business. We specialize in the transportation of radioactive materials across North America. The site is mostly for information about our company and will not be used to attract business but will be used to attract employee's mainly drivers. Driver's are very hard to find in our area. One of the pages needs to be a job's posting page with an apply now button. Either an application can be filled out there or a resume can be uploaded which ever functionality works better. I would like a website that I can easily edit, ability to change text and photos.

Number of Pages Required

5+ page

Colors

Designer to choose colors to be used in the design.

Requirements
Must have
• Home - About - Services - Jobs - Contact pages
• A way prospective employee's can apply or upload their resume to be emailed to me
• Very clean apperance
Should not have
• I don't want it to be busy

```html
<!DOCTYPE html>
<html lang="en">
<head>
<meta charset="utf-8">
<title>Ridgeline Haul Carriers</title>
<link href="https://fonts.googleapis.com/css2?family=Roboto:wght@400;500;700&display=swap" rel="stylesheet">
<style>
:root{
  --blue:#1a5fb4;
  --blue-dark:#0e3f86;
  --navy:#12233f;
  --ink:#222;
  --muted:#666;
  --light:#f1f2f4;
  --white:#fff;
}
*{box-sizing:border-box;margin:0;padding:0}
html,body{width:1200px;height:3780px;overflow:hidden}
body{font-family:'Roboto',sans-serif;color:var(--ink);background:var(--white);position:relative}
.btn{display:inline-block;border-radius:20px;font-size:13px;font-weight:500;letter-spacing:.5px;padding:10px 26px}
.btn-blue{background:var(--blue);color:var(--white)}
.btn-outline{border:1.5px solid var(--ink);color:var(--ink)}
.btn-outline-light{border:1.5px solid var(--white);color:var(--white)}
.photo{position:absolute}

/* header */
.site-header{position:absolute;top:0;left:0;width:1200px;height:110px;display:flex;align-items:center;justify-content:space-between;padding:0 40px 0 140px}
.brand{font-size:30px;font-weight:700;color:var(--blue-dark);display:flex;align-items:center;gap:10px}
.brand-dot{width:14px;height:14px;background:var(--blue);border-radius:50%}
.nav{display:flex;gap:28px;font-size:17px;font-weight:500}
.nav a{color:var(--ink)}

/* hero */
.hero{position:absolute;top:110px;left:0;width:1200px;height:700px;background:linear-gradient(180deg,#2a3550 0%,#1c2a45 45%,#3a4660 70%,#1a2336 100%);overflow:hidden}
.hero-inner{position:absolute;top:170px;width:100%;text-align:center;color:var(--white)}
.hero h1{font-size:62px;font-weight:500;margin-bottom:22px}
.hero p{font-size:14px;line-height:1.6;width:620px;margin:0 auto 30px}
.hero .arrow{position:absolute;top:290px;color:var(--white);font-size:26px}
.hero svg{position:absolute;bottom:0;left:0}

/* welcome */
.welcome{position:absolute;top:830px;left:140px;width:920px;height:440px}
.welcome-text{width:420px}
.welcome h3{font-size:28px;font-weight:400;margin-top:30px}
.welcome h2{font-size:36px;font-weight:400;color:var(--blue);margin:4px 0 26px;white-space:nowrap}
.welcome p{width:420px;font-size:15px;line-height:1.7;color:var(--muted);margin-bottom:28px}

/* services */
.services{position:absolute;top:1320px;left:0;width:1200px;height:500px}
.services-panel{position:absolute;left:590px;top:0;width:610px;height:500px;background:var(--blue);color:var(--white);padding:70px 60px 0 60px}
.services-panel h2{font-size:50px;font-weight:400;margin-bottom:24px}
.services-panel p{width:420px;font-size:15px;line-height:1.7;margin-bottom:28px}

/* testimonials */
.testimonials{position:absolute;top:1820px;left:0;width:1200px;height:360px;background:var(--light);display:flex;justify-content:center;gap:90px;padding-top:100px}
.quote{display:flex;gap:26px;width:420px}
.quote-side{display:flex;flex-direction:column;align-items:center;gap:20px}
.avatar{width:116px;height:116px;border-radius:50%;background:linear-gradient(135deg,#9aa6b5,#4b5563)}
.mark{font-size:60px;color:var(--blue);line-height:.6;font-family:Georgia,serif}
.quote p{font-size:15px;line-height:1.6;color:var(--muted)}
.stars{color:var(--blue);font-size:15px;letter-spacing:3px;margin:12px 0 6px}
.quote cite{font-style:normal;font-weight:700;font-size:15px}

/* blog */
.blog{position:absolute;top:2180px;left:0;width:1200px;height:620px}
.blog h2{text-align:center;font-size:42px;font-weight:400;margin-top:70px;margin-bottom:40px}
.cards{display:flex;justify-content:center;gap:38px}
.card{width:286px}
.card-img{width:286px;height:196px;margin-bottom:26px}
.card h4{font-size:15px;font-weight:700;margin-bottom:10px}
.card time{display:block;font-size:13px;color:var(--blue);font-weight:700;margin-bottom:10px}
.card p{font-size:14px;line-height:1.6;color:var(--muted)}

/* jobs */
.jobs{position:absolute;top:2800px;left:0;width:1200px;height:440px;background:linear-gradient(180deg,#5d6470,#30363f);overflow:hidden}
.jobs-inner{position:absolute;top:90px;width:100%;text-align:center;color:var(--white)}
.jobs h2{font-size:50px;font-weight:400;margin-bottom:24px}
.jobs p{width:880px;margin:0 auto 30px;font-size:15px;line-height:1.7}
.jobs svg{position:absolute;left:0}

/* footer */
.site-footer{position:absolute;top:3240px;left:0;width:1200px;height:460px;background:var(--light);display:flex;padding:130px 0 0 120px;gap:60px}
.footer-brand .brand{font-size:26px;margin-bottom:22px}
.socials{display:flex;gap:10px;padding-left:20px}
.socials span{width:28px;height:28px;border:1.5px solid var(--ink);border-radius:50%}
.site-footer h4{font-size:24px;font-weight:500;margin-bottom:16px}
.newsletter{width:300px}
.newsletter p{font-size:13px;line-height:1.6;color:var(--muted);margin-bottom:16px}
.field{width:190px;height:34px;border-radius:17px;background:var(--white);border:1px solid #ccc;font-size:12px;color:#999;padding:9px 16px;margin-bottom:14px}
.links{width:130px}
.links li{list-style:none;font-size:14px;line-height:2;color:var(--ink)}
.contact li{list-style:none;display:flex;gap:14px;font-size:13px;line-height:1.5;margin-bottom:14px;color:var(--ink)}
.contact .ic{width:30px;height:30px;background:var(--navy);border-radius:4px;flex:none;display:flex;align-items:center;justify-content:center}
.copyright{position:absolute;top:3700px;left:0;width:1200px;height:80px;border-top:1px solid #ddd;display:flex;align-items:center;justify-content:center;font-size:14px;color:var(--muted)}
</style>
</head>
<body>

<header class="site-header">
  <div class="brand"><span class="brand-dot"></span>Ridgeline Haul Carriers</div>
  <nav class="nav"><a>HOME</a><a>ABOUT US</a><a>SERVICES</a><a>JOBS</a><a>CONTACT US</a></nav>
</header>

<section class="hero" role="img" aria-label="City skyline at night with a lit highway">
  <span class="arrow" style="left:14px">&#8249;</span>
  <span class="arrow" style="right:14px">&#8250;</span>
  <div class="hero-inner">
    <h1>Ridgeline Haul Carriers</h1>
    <p>Safe, licensed hauling of sensitive freight across North America. Our drivers are trained, certified and proud of every mile. We keep cargo moving on time and keep every road we travel safer.</p>
    <span class="btn btn-blue">GET MORE INFO</span>
  </div>
  <svg width="1200" height="200" viewBox="0 0 1200 200" preserveAspectRatio="none">
    <path d="M0 130 C300 10 700 230 1200 60 L1200 200 L0 200Z" fill="var(--blue)"/>
    <path d="M0 160 C320 60 720 240 1200 110 L1200 200 L0 200Z" fill="var(--white)"/>
  </svg>
</section>

<section class="welcome">
  <div class="welcome-text">
    <h3>Welcome to</h3>
    <h2>Ridgeline Haul Carriers</h2>
    <p>We are a family run carrier moving regulated freight with care. Every route is planned, every load is tracked, and every driver is backed by a team that knows the work and values the people doing it.</p>
    <span class="btn btn-outline">READ MORE</span>
  </div>
  <div class="photo" role="img" aria-label="Driver's hands on a truck gear shift" style="left:450px;top:30px;width:470px;height:390px;background:linear-gradient(135deg,#8a8f96,#3f4348)"></div>
</section>

<section class="services">
  <div class="photo" role="img" aria-label="Semi truck with tanker trailer parked by bare trees" style="left:0;top:0;width:590px;height:500px;background:linear-gradient(180deg,#b9c2cc 0%,#8d949b 55%,#5e6168 100%)"></div>
  <div class="services-panel">
    <h2>Our Services</h2>
    <p>Licensed long haul transport for controlled materials, dedicated routes and secure handling. We follow strict safety rules from pickup to delivery, with trained crews and modern equipment on every trip.</p>
    <span class="btn btn-outline-light">READ MORE</span>
  </div>
</section>

<section class="testimonials">
  <div class="quote">
    <div class="quote-side"><div class="avatar" role="img" aria-label="Portrait of a customer"></div><span class="mark">&ldquo;</span></div>
    <div><p>Reliable team and clear communication on every load. Our shipments arrive on schedule and the drivers treat the job seriously.</p>
      <div class="stars">&#9733;&#9733;&#9733;&#9733;&#9733;</div><cite>Dalton, Ridgeline Haul Carriers</cite></div>
  </div>
  <div class="quote">
    <div class="quote-side"><div class="avatar" role="img" aria-label="Portrait of a driver"></div><span class="mark">&ldquo;</span></div>
    <div><p>Great place to drive. Fair pay, good trucks and a dispatch crew that has your back out on the road every day.</p>
      <div class="stars">&#9733;&#9733;&#9733;&#9733;&#9733;</div><cite>Dalton, Ridgeline Haul Carriers</cite></div>
  </div>
</section>

<section class="blog">
  <h2>Latest Blog</h2>
  <div class="cards">
    <article class="card"><div class="card-img" role="img" aria-label="Hands reviewing paperwork" style="background:linear-gradient(135deg,#c9ccd1,#7f8790)"></div>
      <h4>NEW ROUTES OPEN THIS FALL</h4><time>&#128197; OCTOBER 17, 2019</time>
      <p>We are adding routes across the region and need drivers ready to start soon.</p></article>
    <article class="card"><div class="card-img" role="img" aria-label="Driver at the steering wheel" style="background:linear-gradient(135deg,#9aa1a8,#454a50)"></div>
      <h4>SAFETY FIRST ON THE ROAD</h4><time>&#128197; OCTOBER 17, 2019</time>
      <p>How our training keeps drivers and cargo safe through every season of travel.</p></article>
    <article class="card"><div class="card-img" role="img" aria-label="Highway interchange lit at night" style="background:linear-gradient(135deg,#2b3a5a,#c47a2c)"></div>
      <h4>LIFE AS A LONG HAUL DRIVER</h4><time>&#128197; OCTOBER 17, 2019</time>
      <p>Our drivers share what a typical week looks like and why they stay with us.</p></article>
  </div>
</section>

<section class="jobs" role="img" aria-label="Dim office with desks behind the jobs banner">
  <svg width="1200" height="90" viewBox="0 0 1200 90" preserveAspectRatio="none" style="top:0">
    <path d="M0 0 L1200 0 L1200 30 C800 90 400 0 0 40Z" fill="var(--white)"/>
  </svg>
  <div class="jobs-inner">
    <h2>Jobs</h2>
    <p>We are hiring experienced class A drivers who take pride in safe, careful work. Competitive pay, home time and full benefits. Send your details or upload a resume and our team will contact you within a few days.</p>
    <span class="btn btn-blue">Apply Now &#8594;</span>
  </div>
  <svg width="1200" height="130" viewBox="0 0 1200 130" preserveAspectRatio="none" style="bottom:0">
    <path d="M0 30 C400 140 800 -20 1200 70 L1200 130 L0 130Z" fill="var(--blue)"/>
    <path d="M0 70 C400 160 820 20 1200 110 L1200 130 L0 130Z" fill="var(--light)"/>
  </svg>
</section>

<footer class="site-footer">
  <div class="footer-brand">
    <div class="brand"><span class="brand-dot"></span>Ridgeline Haul</div>
    <div class="socials"><span></span><span></span><span></span></div>
  </div>
  <div class="newsletter">
    <h4>Sign up for newsletter</h4>
    <p>Get company news, new routes and open driver positions sent to your inbox.</p>
    <div class="field">Your email</div>
    <span class="btn btn-blue" style="background:var(--navy);padding:8px 22px;font-size:12px">SUBSCRIBE</span>
  </div>
  <div class="links">
    <h4>Quick Links</h4>
    <ul><li>Home</li><li>About Us</li><li>Services</li><li>Jobs</li><li>Contact Us</li></ul>
  </div>
  <div class="contact">
    <h4>Contact Us</h4>
    <ul>
      <li><span class="ic"><svg width="14" height="18" viewBox="0 0 14 18"><path d="M7 0C3 0 0 3 0 7c0 5 7 11 7 11s7-6 7-11c0-4-3-7-7-7zm0 10a3 3 0 110-6 3 3 0 010 6z" fill="#fff"/></svg></span><span>Ridgeline Haul Carriers<br>480 Cedar Pass Road, Suite 12<br>Boulder Flats, CO 80000</span></li>
      <li><span class="ic"><svg width="16" height="16" viewBox="0 0 16 16"><path d="M3 1l3 3-2 2c1 2 3 4 5 5l2-2 3 3-2 3C6 15 1 10 0 3z" fill="#fff"/></svg></span><span>Phone :<br>1-555-014-2280</span></li>
      <li><span class="ic"><svg width="16" height="12" viewBox="0 0 16 12"><rect width="16" height="12" fill="#fff"/><path d="M0 0l8 7 8-7" stroke="#12233f" fill="none"/></svg></span><span>Email :<br>hello@ridgelinehaul.example</span></li>
    </ul>
  </div>
</footer>
<div class="copyright">&copy; Copyright 2019 Ridgeline Haul Carriers. All Rights Reserved.</div>

</body>
</html>
```